Classy, Elegant, Simple Business Card Design

Looking to have a classy, simple, and elegant design. Want a top notch designed business card. I really like the look of the new torvane credit card. I also like the design I attached. I am trying to reach 21-29 year old females for booking us for there wedding or event. We offer Disc Jockey Service, Photo Booth Rentals, and Uplighting .

Target Market(s)

21-28 year old females

Contact Information for Business Card

Has to have logo, website, email, and phone number

Font styles to use
Other font styles liked:
• open to font choice, modern, clean
Designer to choose
33a6d7
0791cd
0555a3
ffffff

Requirements
Must have
• Has to have logo, website, email, and phone number
Nice to have
• I really like the design of the new torvane credit card. I also included my logo and some designs I like
Should not have
• clutter or too much info

```html
<!DOCTYPE html>
<html lang="en">
<head>
<meta charset="utf-8">
<title>Tidecrest Event Group – Business Card</title>
<link rel="stylesheet" href="https://fonts.googleapis.com/css2?family=Jost:wght@300;400;500&display=swap">
<style>
  :root {
    --backdrop: #404040;
    --card: #242424;
    --silver: #cfcfcf;
    --silver-dark: #8a8a8a;
    --blue: #1f7ac8;
    --white: #ffffff;
    --muted: #b5b5b5;
  }
  * { margin: 0; padding: 0; box-sizing: border-box; }
  html, body {
    width: 1200px; height: 900px; overflow: hidden;
    background: var(--backdrop);
    font-family: "Jost", "Helvetica Neue", Arial, sans-serif;
  }
  .card {
    position: absolute;
    left: 297px;
    width: 608px; height: 348px;
    border-radius: 22px;
    background: var(--card);
  }
  .card--front { top: 84px; }
  .card--back { top: 468px; }

  /* Front */
  .brand-mark {
    position: absolute; left: 0; right: 0; top: 80px;
    display: flex; flex-direction: column; align-items: center;
    color: var(--silver); font-weight: 400;
  }
  .brand-mark__dot {
    width: 104px; height: 104px; border-radius: 50%;
    background: var(--silver-dark);
    margin-bottom: 26px;
  }
  .brand-mark__name {
    font-size: 38px; letter-spacing: 1px; line-height: 1;
  }
  .brand-mark__sub {
    font-size: 16px; letter-spacing: 7px; line-height: 1; margin-top: 8px;
    padding-left: 7px;
  }

  /* Back */
  .wordmark {
    position: absolute; left: 42px; top: 152px; width: 206px;
    display: flex; flex-direction: column; align-items: center;
    color: var(--blue); font-weight: 300;
  }
  .wordmark__name { font-size: 27px; letter-spacing: 1px; line-height: 1; }
  .wordmark__sub { font-size: 13px; letter-spacing: 5px; line-height: 1; margin-top: 6px; padding-left: 5px; }

  .contact {
    position: absolute; left: 289px; top: 118px;
    color: var(--white);
  }
  .contact__name {
    color: var(--blue); font-size: 21px; font-weight: 500; letter-spacing: 0.4px;
    margin-bottom: 14px;
  }
  .contact__list { list-style: none; }
  .contact__item {
    display: flex; align-items: center; gap: 10px;
    font-size: 16px; font-weight: 400; height: 24.5px; letter-spacing: 0.2px;
  }
  .contact__icon { width: 16px; height: 16px; fill: var(--blue); flex: none; }
</style>
</head>
<body>
  <section class="card card--front">
    <div class="brand-mark">
      <span class="brand-mark__dot"></span>
      <span class="brand-mark__name">TIDECREST</span>
      <span class="brand-mark__sub">EVENT GROUP</span>
    </div>
  </section>

  <section class="card card--back">
    <div class="wordmark">
      <span class="wordmark__name">TIDECREST</span>
      <span class="wordmark__sub">EVENT GROUP</span>
    </div>
    <div class="contact">
      <p class="contact__name">Daniel R. Hale</p>
      <ul class="contact__list">
        <li class="contact__item">
          <svg class="contact__icon" viewBox="0 0 16 16" aria-hidden="true"><path d="M3.6 1.2l2.2 2.6-1.3 1.8c.9 2 2.4 3.5 4.4 4.4l1.8-1.3 2.6 2.2-1.1 2.5C6.6 13.4 2.6 9.4 1.1 3.8z"/></svg>
          <span>555 014 2290</span>
        </li>
        <li class="contact__item">
          <svg class="contact__icon" viewBox="0 0 16 16" aria-hidden="true"><path d="M1 3h14v1.2L8 8.6 1 4.2z"/><path d="M1 5.8l7 4.4 7-4.4V13H1z"/></svg>
          <span>hello@tidecresteventgroup.com</span>
        </li>
        <li class="contact__item">
          <svg class="contact__icon" viewBox="0 0 16 16" aria-hidden="true"><circle cx="8" cy="8" r="7"/><path d="M4 4.5c1.5.2 2.4 1.2 2 2.5-.5 1-2 1-1.6 2.6.3 1 1 1.4.8 2.8M10 2.2c-.4 1.3.6 2 1.6 2.3 1 .3 1 1.6.2 2.2-.8.7-.4 1.8.6 2.1" stroke="var(--card)" stroke-width="1.1" fill="none"/></svg>
          <span>www.tidecresteventgroup.com</span>
        </li>
      </ul>
    </div>
  </section>
</body>
</html>
```